Stylish Business Cards Wanted

- DOUBLE SIDED Design Required -

High end, edgy cards for a corporate and personal stylist. Must include logo,
Name: Belinda Harwick
Title: Director and Stylist
telephone : +61 8 7142 5809
email: belinda@theloombriefing.example
website: theloombriefing.example
Tag: Corporate Workwear & Uniform Specialist | Personal Stylist
Would like nice icons for telephone, email, website

Target Market(s)

Businesses wanting stylish uniforms, people wanting stylish wardrobes

Industry/Entity Type

Corporate Workwear Stylist

Contact Information for Business Card

I would like black, white and gold foiling incorporated in the design - possibly a touch of the other colours on my branding guide attached Name: Belinda Harwick Title: Director and Stylist telephone : +61 8 7142 5809 email: belinda@theloombriefing.example website: theloombriefing.example Tag: Corporate Workwear & Uniform Specialist | Personal Stylist Would like nice icons for telephone, email, website

Font styles to use
Other font styles liked:
• Raleway

Colors

Designer to choose colors to be used in the design.

Requirements
Must have
• Gold foil accents

```html
<!DOCTYPE html>
<html lang="en">
<head>
<meta charset="utf-8">
<title>Belinda Harwick – Business Cards</title>
<link href="https://fonts.googleapis.com/css2?family=Raleway:wght@300;400;700&display=swap" rel="stylesheet">
<style>
  :root {
    --backdrop: #3d3d3e;
    --card-black: #221f20;
    --card-white: #ececec;
    --ink-dark: #1e1c1d;
    --ink-light: #ffffff;
    --ink-muted: #cfcfcf;
    --gold: #c9a45a;
    --gold-light: #e6cb8c;
  }
  * { margin: 0; padding: 0; box-sizing: border-box; }
  html, body {
    width: 1200px; height: 960px; overflow: hidden;
    background: var(--backdrop);
    font-family: 'Raleway', sans-serif;
  }
  .sheet {
    width: 1200px; height: 960px;
    display: flex; align-items: center; justify-content: center; gap: 44px;
  }
  .card {
    position: relative;
    width: 520px; height: 300px;
    border-radius: 26px;
    overflow: hidden;
    box-shadow: 0 14px 30px rgba(0,0,0,0.35);
  }

  /* Back side: white */
  .card--back { background: var(--card-white); color: var(--ink-dark); }
  .gold-rule {
    position: absolute; left: 40px; top: 148px;
    width: 60px; height: 2px;
    background: linear-gradient(90deg, var(--gold), var(--gold-light), var(--gold));
  }
  .tagline {
    position: absolute; left: 40px; top: 116px;
    font-size: 15.5px; font-weight: 400; letter-spacing: 0.2px;
  }
  .contact-list {
    position: absolute; left: 40px; right: 30px; bottom: 30px;
    display: grid; grid-template-columns: 150px 1fr; row-gap: 12px;
    list-style: none;
  }
  .contact-item { display: flex; align-items: center; gap: 9px; font-size: 11.5px; font-weight: 400; }
  .contact-icon {
    width: 20px; height: 20px; border-radius: 4px;
    background: var(--ink-dark);
    display: flex; align-items: center; justify-content: center;
    flex-shrink: 0;
  }

  /* Front side: black */
  .card--front { background: var(--card-black); color: var(--ink-light); }
  .identity { position: absolute; left: 40px; top: 142px; }
  .identity__name { font-size: 23px; font-weight: 400; letter-spacing: 0.3px; line-height: 1; }
  .identity__name strong { font-weight: 700; }
  .identity__title { font-size: 12.5px; font-weight: 300; margin-top: 7px; color: var(--ink-muted); line-height: 1.2; }
  .divider {
    position: absolute; left: 160px; right: 0; top: 179px;
    height: 1px;
    background: linear-gradient(90deg, var(--gold), var(--gold-light), var(--gold));
  }
  .brand {
    position: absolute; right: 34px; top: 132px;
    display: flex; align-items: center; gap: 8px;
    font-size: 16px; font-weight: 400; color: var(--gold-light);
  }
  .brand__dot { width: 8px; height: 8px; border-radius: 50%; background: var(--gold); }
</style>
</head>
<body>
<main class="sheet">
  <section class="card card--back" aria-label="Business card back">
    <p class="tagline">Corporate Workwear &amp; Uniform Specialist | Personal Stylist</p>
    <div class="gold-rule"></div>
    <ul class="contact-list">
      <li class="contact-item">
        <span class="contact-icon">
          <svg width="12" height="12" viewBox="0 0 24 24" aria-hidden="true"><path fill="#e6cb8c" d="M6.6 10.8a15.1 15.1 0 0 0 6.6 6.6l2.2-2.2a1 1 0 0 1 1-.25 11.4 11.4 0 0 0 3.6.57 1 1 0 0 1 1 1V20a1 1 0 0 1-1 1A17 17 0 0 1 3 4a1 1 0 0 1 1-1h3.5a1 1 0 0 1 1 1c0 1.25.2 2.45.57 3.57a1 1 0 0 1-.25 1z"/></svg>
        </span>
        +61 8 7142 5809
      </li>
      <li class="contact-item">
        <span class="contact-icon">
          <svg width="12" height="12" viewBox="0 0 24 24" aria-hidden="true"><circle cx="12" cy="12" r="9.5" fill="none" stroke="#e6cb8c" stroke-width="1.8"/><ellipse cx="12" cy="12" rx="4.2" ry="9.5" fill="none" stroke="#e6cb8c" stroke-width="1.6"/><path d="M2.5 12h19" stroke="#e6cb8c" stroke-width="1.6"/></svg>
        </span>
        theloombriefing.example
      </li>
      <li class="contact-item">
        <span class="contact-icon">
          <svg width="12" height="12" viewBox="0 0 24 24" aria-hidden="true"><rect x="2" y="5" width="20" height="14" rx="1.5" fill="#e6cb8c"/><path d="M2.5 6l9.5 7 9.5-7" fill="none" stroke="#1e1c1d" stroke-width="1.8"/></svg>
        </span>
        belinda@theloombriefing.example
      </li>
    </ul>
  </section>

  <section class="card card--front" aria-label="Business card front">
    <div class="identity">
      <h1 class="identity__name"><strong>BELINDA</strong> Harwick</h1>
      <p class="identity__title">Director &amp; Stylist</p>
    </div>
    <div class="divider"></div>
    <div class="brand">
      <span class="brand__dot"></span>
      <span class="brand__name">The Loom Briefing</span>
    </div>
  </section>
</main>
</body>
</html>
```